Awesome photographers card for an awesome new business

Double sided business card Black background and silver logo in middle on one side. Details on otherside. please keep it simple

Industry/Entity Type

Photographer

Contact Information for Business Card

Gerald Fenwick
0452817360
GeraldFenwickPhotography47@mailbox.test
www.GeraldFenwickPhotography.test.au
Instagram _Gerald_fenwick

Requirements
Must have
• My logo in Silver
• please use instagram logo instead of "Instagram"

```html
<!DOCTYPE html>
<html lang="en">
<head>
<meta charset="utf-8">
<title>Gerald Fenwick Photography – Business Card</title>
<link href="https://fonts.googleapis.com/css2?family=Open+Sans:wght@400;700&display=swap" rel="stylesheet">
<style>
  :root {
    --stage: #2a2a2a;
    --paper: #ffffff;
    --ink: #1a1a1a;
    --panel: #111111;
    --silver: #a6a6a6;
    --silver-dark: #8a8a8a;
    --frame: #d8d8d8;
  }
  * { margin: 0; padding: 0; box-sizing: border-box; }
  html, body {
    width: 1200px; height: 900px; overflow: hidden;
    background: var(--stage);
    font-family: "Open Sans", Arial, sans-serif;
  }
  .canvas {
    width: 1200px; height: 900px;
    display: flex; flex-direction: column;
    align-items: center; justify-content: center; gap: 40px;
  }
  .card {
    width: 700px; height: 400px;
    position: relative; overflow: hidden;
    background: var(--paper);
    box-shadow: 0 10px 30px rgba(0,0,0,.45);
  }

  /* Front side */
  .card-front .brand-mark {
    position: absolute; left: 50%; top: 150px;
    transform: translate(-50%, -50%);
    width: 170px; height: 170px;
    display: flex; align-items: center; justify-content: center;
  }
  .brand-mark .ring {
    position: absolute; inset: 0;
    border: 3px solid var(--silver); border-radius: 50%;
  }
  .brand-mark .brand-name {
    color: var(--silver-dark); font-weight: 700;
    font-size: 19px; letter-spacing: 1px; text-align: center; line-height: 1.2;
  }
  .card-front .site-url {
    position: absolute; left: 0; right: 0; bottom: 48px;
    text-align: center; color: #444;
    font-size: 15px; letter-spacing: 2.4px;
  }

  /* Back side */
  .card-back .dark-panel {
    position: absolute; left: 0; top: 0; width: 100%; height: 240px;
    background: linear-gradient(160deg, #1c1c1c 0%, var(--panel) 60%, #050505 100%);
  }
  .dark-panel .corner-frame { position: absolute; inset: 0; }
  .dark-panel .panel-name {
    position: absolute; left: 50%; top: 120px;
    transform: translate(-50%, -50%);
    color: var(--silver); font-weight: 700; font-size: 38px;
    letter-spacing: 1px; white-space: nowrap;
  }
  .card-back .contact {
    position: absolute; left: 0; right: 0; top: 258px;
    text-align: center; color: var(--ink); font-size: 15px; line-height: 1.32;
  }
  .contact .holder-name {
    font-weight: 700; font-size: 18px; text-transform: uppercase; letter-spacing: .3px;
    margin-bottom: 2px;
  }
  .contact .handle { display: inline-flex; align-items: center; gap: 6px; }
  .contact .handle-mark {
    width: 12px; height: 12px; background: var(--ink); border-radius: 2px;
  }
</style>
</head>
<body>
  <main class="canvas">
    <section class="card card-front" aria-label="Business card front">
      <div class="brand-mark">
        <span class="ring"></span>
        <span class="brand-name">Gerald<br>Fenwick</span>
      </div>
      <p class="site-url">www.GeraldFenwickPhotography.test.au</p>
    </section>

    <section class="card card-back" aria-label="Business card back">
      <div class="dark-panel">
        <svg class="corner-frame" width="700" height="240" viewBox="0 0 700 240" aria-hidden="true">
          <g fill="none" stroke="var(--frame)" stroke-width="1.5">
            <polyline points="22,44 22,22 44,22"/>
            <polyline points="656,22 678,22 678,44"/>
            <polyline points="22,196 22,218 44,218"/>
            <polyline points="656,218 678,218 678,196"/>
          </g>
        </svg>
        <span class="panel-name">Gerald Fenwick</span>
      </div>
      <div class="contact">
        <p class="holder-name">Gerald Fenwick</p>
        <p>(P) 0452817360</p>
        <p>GeraldFenwickPhotography47@mailbox.test</p>
        <p>www.GeraldFenwickPhotography.test.au</p>
        <p class="handle"><span class="handle-mark" aria-hidden="true"></span>_Gerald_fenwick</p>
      </div>
    </section>
  </main>
</body>
</html>
```